Stationery Design Project for Nimbora, Chicago

Nimbora, a street parking application which helps car drivers find a street parking spot by offering an ideal path along which to look for parking. This path is calculated by our algorithm based on data (e.g. historical data, baseball games schedule, etc.). Along this path the driver will find a spot and will also save 70% of the search time. Customer we target is reg. between 21 and 45 yo.

We envision something young, fresh, bright and original. Slightly abstract maybe. It should represent the idea and elements of finding street parking in the city, e.g. car(s), parking spot, people, city, etc. (just ideas!).

Logo is attached.

Requirement:
- Business Cards (2 Sided Full Color CMYK)
- Letterhead (1 Sided Full Color CMYK)
- Envelope (1 Sided Full Color CMYK)
- Sticker (1 Sided Full Color CMYK), round with a 2inch diameter.

Reason: We're starting to get more and more designs and need more time to look into all of them. Very exciting!! Thanks to everybody!

Hi all, we're in the process of selecting our favs. Though choices!!! Really good submissions. Will keep you posted and sorry for the delay.

Target Market(s)

Car drivers and owners between 21 and 45

Industry/Entity Type

Parking

Requirements
Must have
• Sticker should be round and include company URL nimbora.com and the new logo which we will attach soon.
Should not have
• Should not be too serious or boring.

```html
<!DOCTYPE html>
<html lang="en">
<head>
<meta charset="utf-8">
<title>Nimbora — Business Card</title>
<link rel="stylesheet" href="https://fonts.googleapis.com/css2?family=Open+Sans:wght@400;600;700&display=swap">
<style>
  :root {
    --page-bg: #e9eaec;
    --card-white: #ffffff;
    --ink-dark: #2b2b2b;
    --ink-grey: #555659;
    --band-navy: #1b36a0;
    --band-blue: #1f62c6;
    --band-cyan: #19aee6;
    --mark-blue: #1d4fc0;
    --text-light: #ffffff;
  }
  * { margin: 0; padding: 0; box-sizing: border-box; }
  html, body {
    width: 954px;
    height: 1200px;
    overflow: hidden;
    background: var(--page-bg);
    font-family: "Open Sans", Arial, sans-serif;
  }
  .canvas { position: relative; width: 954px; height: 1200px; }

  .card {
    position: absolute;
    width: 796px;
    background: var(--card-white);
    border-radius: 30px;
    overflow: hidden;
    box-shadow: 0 4px 14px rgba(0,0,0,0.18);
  }
  .card--front { left: 79px; top: 88px; height: 456px; }
  .card--back  { left: 84px; top: 650px; height: 454px; }

  .card__band { position: absolute; inset: 0; width: 100%; height: 100%; }

  .brand { position: absolute; display: flex; align-items: center; }
  .brand__dot {
    border-radius: 50%;
    background: var(--mark-blue);
    flex: none;
  }
  .brand__name {
    font-weight: 600;
    color: var(--ink-dark);
    letter-spacing: -1px;
    line-height: 1;
  }
  .card--front .brand { left: 127px; top: 55px; gap: 58px; }
  .card--front .brand__dot { width: 124px; height: 124px; }
  .card--front .brand__name { font-size: 90px; }
  .card--back .brand { left: 109px; top: 97px; gap: 58px; }
  .card--back .brand__dot { width: 126px; height: 126px; }
  .card--back .brand__name { font-size: 104px; }

  .holder {
    position: absolute;
    left: 0; right: 0; top: 212px;
    text-align: center;
    color: var(--ink-grey);
    font-weight: 700;
    font-size: 23px;
  }
  .holder__role { font-size: 18px; font-weight: 600; }

  .contact { position: absolute; color: var(--text-light); font-size: 20px; line-height: 36px; }
  .contact b { font-weight: 700; }
  .contact--phones { right: 398px; top: 316px; text-align: right; }
  .contact--divider {
    position: absolute; left: 415px; top: 297px;
    width: 1.5px; height: 102px; background: rgba(255,255,255,0.85);
  }
  .contact--address { left: 429px; top: 322px; line-height: 32px; }
  .contact--web { left: 0; right: 0; text-align: center; }
  .card--front .contact--web { top: 405px; }
  .card--back .contact--web { top: 395px; }
</style>
</head>
<body>
<main class="canvas">

  <section class="card card--front" aria-label="Business card front">
    <svg class="card__band" viewBox="0 0 796 456" preserveAspectRatio="none" aria-hidden="true">
      <defs>
        <linearGradient id="bandFront" x1="0" x2="1" y1="0" y2="0">
          <stop offset="0" stop-color="var(--band-navy)"/>
          <stop offset="0.25" stop-color="var(--band-blue)"/>
          <stop offset="0.5" stop-color="var(--band-cyan)"/>
          <stop offset="0.75" stop-color="var(--band-blue)"/>
          <stop offset="1" stop-color="var(--band-navy)"/>
        </linearGradient>
        <linearGradient id="edgeFront" x1="0" x2="1" y1="0" y2="0">
          <stop offset="0" stop-color="#111" stop-opacity="0"/>
          <stop offset="0.5" stop-color="#111" stop-opacity="0.9"/>
          <stop offset="1" stop-color="#111" stop-opacity="0"/>
        </linearGradient>
      </defs>
      <path d="M0,212 Q398,290 796,232 L796,456 L0,456 Z" fill="url(#bandFront)"/>
      <path d="M0,214 Q398,292 796,234" fill="none" stroke="url(#edgeFront)" stroke-width="5"/>
    </svg>

    <div class="brand">
      <span class="brand__dot"></span>
      <span class="brand__name">Nimbora</span>
    </div>

    <p class="holder">Your Name - <span class="holder__role">Designation</span></p>

    <p class="contact contact--phones"><b>t</b> : 123-456-7890<br><b>c</b> : 123-456-7890</p>
    <span class="contact--divider"></span>
    <p class="contact contact--address">City Name, Street Name<br>State Name, Country Code</p>
    <p class="contact contact--web"><b>e</b> : name@website.com &nbsp;<b>w</b> : www.website.com</p>
  </section>

  <section class="card card--back" aria-label="Business card back">
    <svg class="card__band" viewBox="0 0 796 454" preserveAspectRatio="none" aria-hidden="true">
      <defs>
        <linearGradient id="bandBack" x1="0" x2="1" y1="0" y2="0">
          <stop offset="0" stop-color="var(--band-navy)"/>
          <stop offset="0.25" stop-color="var(--band-blue)"/>
          <stop offset="0.5" stop-color="var(--band-cyan)"/>
          <stop offset="0.75" stop-color="var(--band-blue)"/>
          <stop offset="1" stop-color="var(--band-navy)"/>
        </linearGradient>
        <linearGradient id="edgeBack" x1="0" x2="1" y1="0" y2="0">
          <stop offset="0" stop-color="#111" stop-opacity="0"/>
          <stop offset="0.5" stop-color="#111" stop-opacity="0.9"/>
          <stop offset="1" stop-color="#111" stop-opacity="0"/>
        </linearGradient>
      </defs>
      <path d="M0,308 Q398,393 796,305 L796,454 L0,454 Z" fill="url(#bandBack)"/>
      <path d="M0,310 Q398,395 796,307" fill="none" stroke="url(#edgeBack)" stroke-width="5"/>
    </svg>

    <div class="brand">
      <span class="brand__dot"></span>
      <span class="brand__name">Nimbora</span>
    </div>

    <p class="contact contact--web"><b>e</b> : name@website.com &nbsp;<b>w</b> : www.website.com</p>
  </section>

</main>
</body>
</html>
```